Upmarket Dessert Lounge needs a Business Card Design

We are an upmarket dessert lounge needing a business card to match our image.

We want something that is simple yet beautiful, feminine, classy, sophisticated and elegant. We want it to stand out and don't mind if it is bold.

The design should include our logo and colours of red or maroon with gold highlights. We don't mind if black is used.

Marlow & Quince

Target Market(s)

For those who like to indulge or treat themselves and give in to their temptations on good quality desserts.

Industry/Entity Type

Business

Requirements
Must have
• Must include our logo and our name

Marlow & Quince

M & Q

```html
<!DOCTYPE html>
<html lang="en">
<head>
<meta charset="utf-8">
<title>Marlow &amp; Quince — Business Card</title>
<link rel="stylesheet" href="https://fonts.googleapis.com/css2?family=Crimson+Text:wght@400;700&family=PT+Sans:wght@400&display=swap">
<style>
  :root {
    --maroon: #7a1418;
    --maroon-deep: #5e0f12;
    --cream: #f6d7a6;
    --white: #ffffff;
    --ink: #2b2b2b;
    --backdrop: #4a2e1f;
  }
  * { box-sizing: border-box; margin: 0; padding: 0; }
  html, body {
    width: 1200px; height: 758px; overflow: hidden;
    background: var(--backdrop);
  }
  .stage { position: relative; width: 1200px; height: 758px; }
  .card {
    position: absolute;
    width: 520px; height: 297px;
    border-radius: 22px;
    overflow: hidden;
    box-shadow: 0 8px 18px rgba(0,0,0,0.35);
  }
  /* front */
  .card-front { left: 50px; top: 220px; background: var(--white); }
  .card-front .wave { position: absolute; inset: 0; }
  .brand-name {
    position: absolute; left: 34px; top: 48px;
    font-family: "Crimson Text", serif; font-weight: 700;
    font-size: 34px; color: var(--maroon); letter-spacing: 0.5px;
  }
  .address {
    position: absolute; left: 24px; top: 160px;
    font-family: "PT Sans", sans-serif; font-size: 12.5px; color: var(--ink);
  }
  .person {
    position: absolute; left: 24px; top: 188px;
    font-family: "Crimson Text", serif; font-size: 19px; color: var(--ink);
  }
  .person strong { font-weight: 700; letter-spacing: 0.5px; }
  .person .title { font-family: "PT Sans", sans-serif; font-size: 13px; }
  .contact {
    position: absolute; right: 26px; top: 150px;
    list-style: none; text-align: right;
    font-family: "PT Sans", sans-serif; font-size: 12.5px; color: var(--white);
    line-height: 18px;
  }
  .contact li { display: flex; justify-content: flex-end; align-items: center; gap: 5px; }
  .contact svg { width: 10px; height: 10px; fill: var(--white); flex: none; }
  /* back */
  .card-back { left: 630px; top: 240px; background: var(--maroon); }
  .monogram {
    position: absolute; left: 0; right: 0; top: 62px; text-align: center;
    font-family: "Crimson Text", serif; font-weight: 400;
    font-size: 92px; line-height: 1; color: var(--cream);
  }
  .web {
    position: absolute; left: 0; right: 0; bottom: 40px; text-align: center;
    font-family: "PT Sans", sans-serif; font-size: 20px; letter-spacing: 3px;
    color: var(--white);
  }
</style>
</head>
<body>
<main class="stage">
  <section class="card card-front" aria-label="Business card front">
    <svg class="wave" viewBox="0 0 520 297" preserveAspectRatio="none" aria-hidden="true">
      <path d="M0,246 C180,246 360,150 520,60 L520,297 L0,297 Z" fill="var(--maroon)"/>
      <path d="M0,240 C180,240 360,144 520,54" fill="none" stroke="var(--cream)" stroke-width="4"/>
    </svg>
    <div class="brand-name">Marlow &amp; Quince</div>
    <p class="address">Street Name, City Name, State Zip Code</p>
    <p class="person"><strong>Your name,</strong> <span class="title">Title</span></p>
    <ul class="contact">
      <li><svg viewBox="0 0 10 10"><path d="M2 0.5 L4 2.5 L3 3.8 Q4.5 6 6.2 7 L7.5 6 L9.5 8 L8 9.5 Q3 9 0.5 2 Z"/></svg>555-018-2740</li>
      <li><svg viewBox="0 0 10 10"><path d="M3 0 H7 V10 H3 Z M3.8 1.2 V7.5 H6.2 V1.2 Z"/></svg>555-018-2740</li>
      <li><svg viewBox="0 0 10 10"><path d="M0 2 H10 V8 H0 Z M0.8 2.6 L5 5.6 L9.2 2.6" stroke="var(--maroon)" stroke-width="0.8"/></svg>hello@marlowquince.com</li>
      <li><svg viewBox="0 0 10 10"><circle cx="5" cy="5" r="4.5"/><path d="M0.5 5 H9.5 M5 0.5 V9.5" stroke="var(--maroon)" stroke-width="0.8"/></svg>www.marlowquince.com</li>
    </ul>
  </section>

  <section class="card card-back" aria-label="Business card back">
    <div class="monogram">M &amp; Q</div>
    <p class="web">www.marlowquince.com</p>
  </section>
</main>
</body>
</html>
```